Need CATCHY/VIVID Banner design for my new UTV/ATV/Off Road Vehicle turn signal/lighting company

I need a banner ad designed so I can advertise on several different ATV (all terrain vehicle), UTV (Utility Vehicles), Golf Cart and Off-Road Vehicle forums. Ads need to be very catchy and produce a call to action. Action is getting hits to my website. Our main business is selling turn signal kits to make your side by side or your ATV/UTV street legal, as some states now allow you to drive these on public roads if you have the following items: Turn Signals, Horn, Lighted license plate bracket, headlights and brake lights. We sell all of these items for just about any model vehicle out there. Our call to action for this banner would be to get more website visits.

Target Market(s)

Off-road/outdoor enthusiasts,

Industry/Entity Type

Car Accessorie

Font styles to use
Sans Serif

Requirements
Must have
• Ad size need to be either 728x90 or 300x250. Colorful ad with an off-road vehicle integrated to the design (think UTV, side-by-side, etc.
Nice to have
• Nice to haves would be anything that makes this banner ad stand out on very boring web pages.
Should not have
• anything dull

```html
<!DOCTYPE html>
<html lang="en">
<head>
<meta charset="utf-8">
<title>Blinkway – ATV Signal Lighting Banner</title>
<link href="https://fonts.googleapis.com/css2?family=Montserrat:wght@800;900&family=Roboto:wght@300;400;700&display=swap" rel="stylesheet">
<style>
  :root {
    --ink: #0b0b0b;
    --white: #ffffff;
    --red-orange: #e63f1e;
    --orange: #f2781c;
    --amber: #f9a417;
    --yellow: #fdc214;
    --arrow-dark: #e9541b;
    --arrow-edge: #f8b46a;
    --box: #f37a1e;
    --vehicle-warm: #c9502e;
    --vehicle-dark: #3a3a3a;
  }
  * { margin: 0; padding: 0; box-sizing: border-box; }
  html, body { width: 1200px; height: 148px; overflow: hidden; background: var(--white); }
  .banner {
    position: relative;
    width: 1200px; height: 148px;
    overflow: hidden;
    background: linear-gradient(90deg, var(--red-orange) 0%, var(--orange) 40%, var(--amber) 72%, var(--yellow) 100%);
    font-family: "Roboto", Arial, sans-serif;
  }
  .brand-panel { position: absolute; left: 0; top: 0; width: 340px; height: 148px; }
  .brand-name {
    position: absolute; left: 0; width: 312px; top: 30px;
    text-align: center;
    font-family: "Montserrat", Arial, sans-serif;
    font-weight: 900; font-size: 40px; letter-spacing: 1px;
    color: var(--yellow);
  }
  .brand-tagline {
    position: absolute; left: 22px; top: 98px; width: 270px;
    font-family: "Montserrat", Arial, sans-serif;
    font-weight: 800; color: var(--white); line-height: 1;
  }
  .brand-tagline .line-main { display: block; font-size: 21px; letter-spacing: -0.3px; }
  .brand-tagline .line-sub { display: block; font-size: 13.5px; margin-top: 4px; letter-spacing: 0.2px; }
  .vehicle {
    position: absolute; border-radius: 18px;
  }
  .vehicle-sport {
    left: 366px; top: 8px; width: 186px; height: 134px;
    background: radial-gradient(ellipse at 50% 45%, #b9b2ab 0%, var(--vehicle-warm) 45%, var(--vehicle-dark) 85%);
  }
  .vehicle-utility {
    left: 976px; top: 6px; width: 214px; height: 138px;
    background: radial-gradient(ellipse at 50% 50%, #5a5a5a 0%, #2b2b2b 60%, #161616 100%);
  }
  .headline-arrow { position: absolute; left: 538px; top: 2px; width: 436px; height: 96px; }
  .headline {
    position: absolute; left: 588px; top: 10px; width: 332px; height: 76px;
    text-align: center; color: var(--white);
  }
  .headline .line-light { display: block; font-weight: 300; font-size: 35px; line-height: 38px; letter-spacing: 0.5px; }
  .headline .line-bold { display: block; font-weight: 700; font-size: 33px; line-height: 36px; letter-spacing: 0.3px; }
  .feature-icons {
    position: absolute; left: 592px; top: 106px; width: 316px; height: 32px;
    display: flex; justify-content: space-between; align-items: center;
  }
  .feature-icons svg { height: 30px; }
</style>
</head>
<body>
<div class="banner">
  <svg class="brand-panel" viewBox="0 0 340 148" aria-hidden="true">
    <path d="M0 0 H300 Q345 74 300 148 H0 Z" fill="var(--white)"/>
    <path d="M0 0 H294 Q337 74 294 148 H0 Z" fill="var(--ink)"/>
  </svg>
  <div class="brand-name">BLINKWAY</div>
  <div class="brand-tagline">
    <span class="line-main">TURN SIGNAL KITS</span>
    <span class="line-sub">&amp; LIGHTING ACCESSORIES</span>
  </div>

  <div class="vehicle vehicle-sport" role="img" aria-label="Sport side-by-side off-road vehicle in grey and red"></div>

  <svg class="headline-arrow" viewBox="0 0 436 96" aria-hidden="true">
    <defs>
      <linearGradient id="arrowFill" x1="0" x2="1">
        <stop offset="0" stop-color="#e4451b"/>
        <stop offset="1" stop-color="#f18a1e"/>
      </linearGradient>
    </defs>
    <polygon points="2,48 60,2 60,22 376,22 376,2 434,48 376,94 376,74 60,74 60,94" fill="url(#arrowFill)" stroke="var(--arrow-edge)" stroke-width="2"/>
    <rect x="50" y="8" width="336" height="80" fill="var(--box)" stroke="var(--arrow-edge)" stroke-width="1.5"/>
  </svg>
  <div class="headline">
    <span class="line-light">ATV VECHICLE</span>
    <span class="line-bold">SIGNAL LIGHTING</span>
  </div>

  <div class="feature-icons">
    <svg viewBox="0 0 40 32" aria-label="Brake light" role="img">
      <circle cx="20" cy="16" r="10" fill="none" stroke="#fff" stroke-width="3"/>
      <path d="M6 6 Q0 16 6 26 M34 6 Q40 16 34 26" fill="none" stroke="#fff" stroke-width="3"/>
      <rect x="18.5" y="9" width="3" height="9" fill="#fff"/><circle cx="20" cy="22" r="1.8" fill="#fff"/>
    </svg>
    <svg viewBox="0 0 40 32" aria-label="Headlight" role="img">
      <path d="M18 4 Q4 4 4 16 Q4 28 18 28 Z" fill="#fff"/>
      <path d="M24 7 H36 M24 13 H36 M24 19 H36 M24 25 H36" stroke="#fff" stroke-width="3"/>
    </svg>
    <svg viewBox="0 0 56 32" aria-label="Horn" role="img">
      <path d="M2 10 L5 6 M1 16 H6 M2 22 L5 26" stroke="#fff" stroke-width="2"/>
      <path d="M9 6 Q14 16 9 26 Q20 18 40 18 L40 14 Q20 14 9 6 Z" fill="none" stroke="#fff" stroke-width="2.5"/>
      <rect x="40" y="12" width="10" height="8" rx="2" fill="#fff"/>
    </svg>
    <svg viewBox="0 0 56 32" aria-label="Turn signals" role="img">
      <path d="M2 16 L16 3 V10 H40 V3 L54 16 L40 29 V22 H16 V29 Z" fill="none" stroke="#fff" stroke-width="2.5" stroke-linejoin="round"/>
    </svg>
    <svg viewBox="0 0 28 34" aria-label="Traffic light" role="img">
      <rect x="8" y="1" width="12" height="32" rx="3" fill="#fff"/>
      <path d="M8 5 H2 L8 11 M8 14 H2 L8 20 M8 23 H2 L8 29 M20 5 H26 L20 11 M20 14 H26 L20 20 M20 23 H26 L20 29" fill="#fff"/>
      <circle cx="14" cy="7" r="3" fill="var(--amber)"/><circle cx="14" cy="17" r="3" fill="var(--amber)"/><circle cx="14" cy="27" r="3" fill="var(--amber)"/>
    </svg>
  </div>

  <div class="vehicle vehicle-utility" role="img" aria-label="Black utility side-by-side vehicle with roof and cargo bed"></div>
</div>
</body>
</html>
```